New Dental Office Needs an Attractive and user friendly Website Designed

I need a website for a new dental office. The Name is Harrowfield Dentistry. I would like a Modern design with a user friendly interface and usability.
I would like a landing page, a page that lists the services we offer: Cosmetic Dentistry, Implants, Dental Hygiene, Emergency Services, Restorations, Dentures
Target Market(s)
Mid to upper class
Industry/Entity Type
Dentistry
Coding
Number of Pages Required
1 page
Requirements
Must have
- Landing page that has a scheduling option, Procedures, operating hours, and contact us info
Nice to have
- Appealing design, Soft comforting colors. Easy to navigate page, Modern and professional.

```html
<!DOCTYPE html>
<html lang="en">
<head>
<meta charset="UTF-8">
<title>Harrowfield Dentistry</title>
<link href="https://fonts.googleapis.com/css2?family=Poppins:wght@400;500;600&display=swap" rel="stylesheet">
<style>
:root{
  --teal:#43b9ad;
  --teal-soft:#6cc8bd;
  --teal-deep:#2f9e93;
  --mist:#eef4f6;
  --ink:#222a2e;
  --muted:#8b969a;
  --line:#d9e2e5;
  --dark:#242424;
  --white:#ffffff;
}
*{box-sizing:border-box;margin:0;padding:0}
html,body{width:1200px;height:4489px;overflow:hidden}
body{font-family:"Poppins",sans-serif;color:var(--ink);background:var(--white);position:relative}
.abs{position:absolute}
.center{text-align:center}
.btn{position:absolute;display:flex;align-items:center;justify-content:center;background:var(--teal);color:var(--white);font-size:13px;font-weight:500;border-radius:4px}
.btn-outline{background:transparent;border:2px solid var(--white)}
.btn-white{background:var(--white);color:var(--teal);font-size:12px}
.photo{position:absolute;overflow:hidden}
.logo{font-size:24px;font-weight:500;color:var(--ink);letter-spacing:.2px}
.nav a{position:absolute;font-size:13px;color:var(--ink);text-decoration:none}
.mark{position:absolute;left:580px;width:40px;height:6px;border-radius:3px;background:var(--teal)}
.section-title{position:absolute;left:0;width:1200px;text-align:center;font-size:31px;font-weight:500}
.service-card{position:absolute;width:277px;height:315px;border:1px solid var(--line);border-radius:10px;overflow:hidden;background:var(--white)}
.service-card .photo{left:0;top:0;width:277px;height:165px}
.service-card .badge{position:absolute;left:96px;top:122px;width:84px;height:84px;border-radius:50%;background:var(--white);border:6px solid #cfeeea}
.service-card h3{position:absolute;top:223px;width:100%;text-align:center;font-size:16px;font-weight:500}
.service-card p{position:absolute;top:252px;left:30px;right:30px;text-align:center;font-size:11px;line-height:14px;color:var(--muted)}
.team-card{position:absolute;top:2435px;width:201px;height:244px;overflow:hidden;border-radius:2px}
.team-card .label{position:absolute;left:14px;right:14px;bottom:14px;height:65px;background:var(--white);border-radius:6px;text-align:center;padding-top:14px}
.team-card .label b{display:block;font-size:14px;font-weight:500}
.team-card .label span{font-size:11px;color:var(--muted)}
.quote{position:absolute;background:var(--white)}
.quote .who{position:absolute;font-size:13px;line-height:19px}
.quote .who b{font-weight:600}
.quote .qm{position:absolute;font-size:62px;line-height:60px;color:var(--teal-soft);font-weight:600}
.quote p{position:absolute;font-size:13px;line-height:19px;color:var(--muted)}
.field{position:absolute;border:1px solid var(--line);border-radius:26px;font-size:12px;color:#6f7a7e;padding:17px 26px}
.foot-nav a{position:absolute;top:4285px;font-size:12px;color:var(--white);text-decoration:none}
.contact-item{position:absolute;top:4330px;display:flex;align-items:center;gap:10px;font-size:12px;color:var(--white)}
.dot-icon{width:24px;height:24px;border-radius:50%;background:var(--teal);display:flex;align-items:center;justify-content:center}
.social{position:absolute;top:4386px;width:18px;height:18px;border-radius:50%;border:2px solid var(--white)}
</style>
</head>
<body>

<!-- Hero -->
<svg class="abs" style="left:0;top:0" width="1200" height="670" viewBox="0 0 1200 670">
  <path d="M0 0H1200V560C1000 620 800 660 590 655C360 650 170 620 0 575Z" fill="var(--mist)"/>
  <path d="M120 605C300 660 480 670 640 655C840 636 1020 600 1150 580C980 625 800 660 600 668C420 672 260 650 120 605Z" fill="var(--teal)"/>
</svg>
<div class="photo" role="img" aria-label="Dentist in blue scrubs treating a smiling patient, with teal leaf shapes behind" style="left:430px;top:85px;width:740px;height:560px;border-radius:0 0 0 40px;background:linear-gradient(135deg,#e2edf1 0%,#a9c6d9 45%,#5f9bc9 75%,#cfe2ec 100%)"></div>

<div class="abs" style="left:100px;top:112px;width:444px;height:444px;border-radius:50%;border:2px solid #d7e7e9"></div>
<div class="abs" style="left:104px;top:118px;width:436px;height:436px;border-radius:50%;background:var(--teal-soft)"></div>
<div class="abs center" style="left:120px;top:246px;width:404px;color:var(--white)">
  <div style="font-size:34px;font-weight:500;line-height:44px">High Quality and</div>
  <div style="font-size:42px;font-weight:500;line-height:50px">Painless Dentistry</div>
  <div style="font-size:15px;line-height:20px;margin-top:10px;opacity:.95">If you are in need of high-quality, professional and friendly dental care, look no further than our clinic.</div>
</div>
<div class="btn btn-outline" style="left:235px;top:430px;width:178px;height:44px">Learn More</div>

<div class="abs logo" style="left:160px;top:24px">Harrowfield Dentistry</div>
<nav class="nav">
  <a style="left:434px;top:32px;color:var(--teal)">Home</a>
  <a style="left:510px;top:32px">About Us</a>
  <a style="left:608px;top:32px">Services</a>
  <a style="left:695px;top:32px">Dentists</a>
  <a style="left:779px;top:32px">Contact Us</a>
</nav>
<div class="btn" style="left:876px;top:23px;width:162px;height:40px">Book Appointment</div>

<!-- Services -->
<div class="mark" style="top:740px"></div>
<h2 class="section-title" style="top:765px">Our Services</h2>

<div class="service-card" style="left:160px;top:843px"><div class="photo" role="img" aria-label="Patient receiving an implant consultation" style="background:linear-gradient(135deg,#dfe6ea,#8fb1cf)"></div><div class="badge"></div><h3>Implants</h3><p>It is a long established fact that a will be distracted.</p></div>
<div class="service-card" style="left:461px;top:843px"><div class="photo" role="img" aria-label="Smiling patient during a hygiene cleaning" style="background:linear-gradient(135deg,#c9d3dc,#9fb5d6)"></div><div class="badge"></div><h3>Dental Hygiene</h3><p>It is a long established fact that a will be distracted.</p></div>
<div class="service-card" style="left:761px;top:843px"><div class="photo" role="img" aria-label="Patient with a bright smile during cosmetic treatment" style="background:linear-gradient(135deg,#b78d7a,#e8ddd6)"></div><div class="badge"></div><h3>Cosmetic Dentistry</h3><p>It is a long established fact that a will be distracted.</p></div>
<div class="service-card" style="left:160px;top:1183px"><div class="photo" role="img" aria-label="Dentist working in a bright treatment room" style="background:linear-gradient(135deg,#e6eaee,#a4bcd0)"></div><div class="badge"></div><h3>Dentures</h3><p>It is a long established fact that a will be distracted.</p></div>
<div class="service-card" style="left:461px;top:1183px"><div class="photo" role="img" aria-label="Urgent dental treatment with gloved hands" style="background:linear-gradient(135deg,#8fb98a,#3f8fd6)"></div><div class="badge"></div><h3>Emergency Services</h3><p>It is a long established fact that a will be distracted.</p></div>
<div class="service-card" style="left:761px;top:1183px"><div class="photo" role="img" aria-label="Dental staff and a happy patient" style="background:linear-gradient(135deg,#6e8fb0,#c7d4e2)"></div><div class="badge"></div><h3>Restorations</h3><p>It is a long established fact that a will be distracted.</p></div>

<!-- About -->
<svg class="abs" style="left:0;top:1570px" width="1200" height="690" viewBox="0 0 1200 690">
  <path d="M0 110C300 40 560 20 760 38C920 52 1080 80 1200 120V560C1000 640 760 680 560 680C340 680 150 640 0 590Z" fill="var(--mist)"/>
  <path d="M600 12C800 0 1000 30 1200 90V110C1060 70 880 34 740 24C700 20 650 16 600 12Z" fill="var(--teal)"/>
  <path d="M0 590C150 640 330 672 600 680C420 690 200 670 0 615Z" fill="var(--teal)"/>
</svg>
<div class="abs" style="left:161px;top:1687px;width:456px;height:452px;border-radius:50%;border:8px solid var(--teal);border-left-color:transparent;border-top-color:transparent;transform:rotate(-15deg)"></div>
<div class="photo" role="img" aria-label="Smiling male patient in the dental chair during a check-up" style="left:161px;top:1687px;width:452px;height:452px;border-radius:50%;background:linear-gradient(135deg,#d5dfe7,#8fb0c8 60%,#cfdbe4)"></div>
<div class="abs" style="left:674px;top:1731px;width:40px;height:6px;border-radius:3px;background:var(--teal)"></div>
<h2 class="abs" style="left:674px;top:1756px;font-size:31px;font-weight:500">About Us</h2>
<div class="abs" style="left:674px;top:1818px;width:370px;font-size:13px;line-height:19.5px;color:#4d585c">
  <p>Welcome to our Harrowfield team dedicated to empowering patients with valuable knowledge and resources.</p>
  <p style="margin-top:14px">It is a long established fact that a reader will be distracted by the readable content of a page when looking at its layout. The point of using Lorem Ipsum is that it has a more-or-less normal distribution of letters, as opposed to using 'Content here, content here', making it look like readable English.</p>
</div>
<div class="btn" style="left:674px;top:2033px;width:160px;height:40px">Learn More</div>

<!-- Team -->
<div class="mark" style="top:2330px"></div>
<h2 class="section-title" style="top:2356px">Meet Our Dental Team</h2>
<div class="team-card" style="left:160px" role="img" aria-label="Portrait of a female dentist in blue scrubs"><div style="position:absolute;inset:0;background:linear-gradient(180deg,#eef2f5,#5b86c4)"></div><div class="label"><b>Dr. Elena Marsh</b><span>Lead Dentist</span></div></div>
<div class="team-card" style="left:387px" role="img" aria-label="Portrait of a male dentist in a white coat"><div style="position:absolute;inset:0;background:linear-gradient(180deg,#dfe4e8,#b9c6d2)"></div><div class="label"><b>Dr. Elena Marsh</b><span>Lead Dentist</span></div></div>
<div class="team-card" style="left:611px" role="img" aria-label="Portrait of a female dentist on a blue background"><div style="position:absolute;inset:0;background:linear-gradient(180deg,#7cc7e6,#3c96d2)"></div><div class="label"><b>Dr. Elena Marsh</b><span>Lead Dentist</span></div></div>
<div class="team-card" style="left:838px" role="img" aria-label="Portrait of a male dentist in a clinic"><div style="position:absolute;inset:0;background:linear-gradient(180deg,#e4e9ec,#aebfcc)"></div><div class="label"><b>Dr. Elena Marsh</b><span>Lead Dentist</span></div></div>
<div class="btn" style="left:519px;top:2719px;width:162px;height:40px">View All Team</div>

<!-- Testimonials -->
<svg class="abs" style="left:0;top:2815px" width="1200" height="720" viewBox="0 0 1200 720">
  <path d="M0 60C250 15 450 5 600 5C800 5 1000 25 1200 60V640C1000 700 800 720 600 715C400 710 200 690 0 650Z" fill="var(--teal)"/>
</svg>
<div class="abs" style="left:580px;top:2882px;width:40px;height:6px;border-radius:3px;background:var(--white)"></div>
<h2 class="section-title" style="top:2910px;color:var(--white)">Our Testimonial</h2>

<div class="quote" style="left:390px;top:2992px;width:490px;height:182px">
  <div class="who" style="left:108px;top:48px">Nora Whitfield<br><b>Caldwell Partners Ltd.</b></div>
  <div class="qm" style="left:276px;top:44px">&ldquo;</div>
  <p style="left:108px;top:104px;width:330px">It was pleasure to work with approhire. it's helped us in our contributed his technical expertise.</p>
</div>
<div class="photo" role="img" aria-label="Portrait of a bearded male client" style="left:320px;top:3013px;width:142px;height:140px;border-radius:60px 0 0 0;background:linear-gradient(180deg,#f3f3f3,#c9d3dc)"></div>

<div class="quote" style="left:322px;top:3205px;width:488px;height:183px">
  <div class="who" style="left:37px;top:48px">Nora Whitfield<br><b>Caldwell Partners Ltd.</b></div>
  <div class="qm" style="left:203px;top:44px">&ldquo;</div>
  <p style="left:37px;top:104px;width:330px">It was pleasure to work with approhire. it's helped us in our contributed his technical expertise.</p>
</div>
<div class="photo" role="img" aria-label="Portrait of a smiling female client" style="left:738px;top:3227px;width:142px;height:140px;border-radius:0 60px 0 0;background:linear-gradient(180deg,#f4f4f4,#d8cfc8)"></div>
<div class="btn btn-white" style="left:512px;top:3435px;width:176px;height:40px">View All Testimonial</div>

<!-- Appointment -->
<div class="mark" style="top:3604px"></div>
<h2 class="section-title" style="top:3630px">Book An Appointment</h2>
<div class="field" style="left:190px;top:3716px;width:402px;height:50px">First Name*</div>
<div class="field" style="left:608px;top:3716px;width:402px;height:50px">Last Name*</div>
<div class="field" style="left:190px;top:3780px;width:402px;height:50px">E-mail*</div>
<div class="field" style="left:608px;top:3780px;width:402px;height:50px">Phone*</div>
<div class="field" style="left:190px;top:3848px;width:820px;height:135px;border-radius:20px">Message*</div>
<div class="btn" style="left:521px;top:4015px;width:162px;height:40px">Book Now</div>

<!-- Footer -->
<svg class="abs" style="left:0;top:4110px" width="1200" height="379" viewBox="0 0 1200 379">
  <path d="M0 70C250 30 450 12 600 12C800 12 1000 30 1200 60V379H0Z" fill="var(--teal)"/>
  <path d="M0 78C250 42 450 26 600 26C800 26 1000 44 1200 72V379H0Z" fill="var(--dark)"/>
</svg>
<div class="abs center logo" style="left:0;top:4196px;width:1200px;color:var(--white)">Harrowfield Dentistry</div>
<nav class="foot-nav">
  <a style="left:381px">Home</a>
  <a style="left:466px">About Us</a>
  <a style="left:567px">Services</a>
  <a style="left:666px">Team</a>
  <a style="left:752px">Contact Us</a>
</nav>
<div class="contact-item" style="left:281px">
  <span class="dot-icon"><svg width="12" height="12" viewBox="0 0 24 24"><path d="M6.6 10.8a15 15 0 0 0 6.6 6.6l2.2-2.2a1 1 0 0 1 1-.25 11 11 0 0 0 3.6.6 1 1 0 0 1 1 1V20a1 1 0 0 1-1 1A17 17 0 0 1 3 4a1 1 0 0 1 1-1h3.5a1 1 0 0 1 1 1 11 11 0 0 0 .6 3.6 1 1 0 0 1-.25 1z" fill="#fff"/></svg></span>+1 555 014 2260</div>
<div class="contact-item" style="left:487px">
  <span class="dot-icon"><svg width="12" height="12" viewBox="0 0 24 24"><rect x="2" y="5" width="20" height="14" rx="2" fill="#fff"/><path d="M3 6l9 7 9-7" stroke="var(--teal)" stroke-width="2" fill="none"/></svg></span>hello@harrowfielddental.com</div>
<div class="contact-item" style="left:747px;top:4325px">
  <span class="dot-icon"><svg width="12" height="12" viewBox="0 0 24 24"><path d="M12 2a7 7 0 0 0-7 7c0 5 7 13 7 13s7-8 7-13a7 7 0 0 0-7-7zm0 9.5A2.5 2.5 0 1 1 12 6.5a2.5 2.5 0 0 1 0 5z" fill="#fff"/></svg></span>122, Lorem ipsum dolird</div>
<div class="social" style="left:549px"></div>
<div class="social" style="left:592px"></div>
<div class="social" style="left:634px"></div>
<div class="abs" style="left:160px;top:4430px;width:878px;height:1px;background:#4a4a4a"></div>
<div class="abs center" style="left:0;top:4452px;width:1200px;font-size:11px;color:var(--white)">Copyright © 2025harrowfield.com. All rights reserved.</div>

</body>
</html>
```